Website Design for Wheels for Servicemen.org - Donated Cars to Disabled Vets

Need a Wordpress website. The coding now, esp. the CDONT coding is not supported by many hosting sites. Looking for a landing page to generate leads.

Logo Text

look at current one for ideas

Coding

Coded - Design and coding required

Number of Pages Required

1 page

Requirements
Must have
• look at current website at www.wheelsforservicemen.org
Nice to have
• look at this site: http://givevehicletoservicemen.org

```html
<!DOCTYPE html>
<html lang="en">
<head>
<meta charset="utf-8">
<title>Wheels for Servicemen – Donate Your Car</title>
<link rel="stylesheet" href="https://fonts.googleapis.com/css2?family=Open+Sans:wght@400;600;700;800&display=swap">
<style>
:root{
  --blue:#1e5aa8;
  --blue-dark:#174a8e;
  --red:#b3191f;
  --red-soft:rgba(176,52,58,.72);
  --orange:#f39c1e;
  --yellow:#f6c22b;
  --sky:#1e9ee0;
  --ink:#333a44;
  --heading:#1e5aa8;
  --white:#ffffff;
  --line:#e3e6ea;
}
*{box-sizing:border-box;margin:0;padding:0}
html,body{width:1200px;height:2731px;overflow:hidden}
body{font-family:"Open Sans",Arial,sans-serif;color:var(--ink);background:var(--white);position:relative}
.abs{position:absolute}

/* header */
.site-header{position:absolute;left:0;top:0;width:1200px;height:115px;background:var(--blue)}
.brand{position:absolute;display:flex;align-items:center;gap:12px;color:var(--white);font-weight:700;font-size:22px}
.brand-dot{width:34px;height:34px;border-radius:50%;background:var(--red)}
.site-header .brand{left:128px;top:38px}
.main-nav{position:absolute;left:440px;top:28px;display:flex}
.nav-item{width:140px;text-align:center;color:var(--white);font-size:12px;font-weight:700;letter-spacing:.3px}
.nav-item svg{display:block;margin:0 auto 12px}
.nav-item.active span{border-bottom:3px solid var(--white);padding-bottom:6px}
.help-box{position:absolute;left:840px;top:0;width:242px;height:115px;background:var(--red);color:var(--white)}
.help-box svg{position:absolute;left:20px;top:16px}
.help-label{position:absolute;left:78px;top:14px;font-size:11px;font-weight:700}
.help-phone{position:absolute;left:78px;top:28px;font-size:21px;font-weight:700}
.help-note{position:absolute;left:78px;top:57px;font-size:11px;font-weight:700}
.help-days{position:absolute;left:0;width:100%;top:84px;text-align:center;font-size:13px;font-weight:800}

/* hero */
.hero{position:absolute;left:0;top:115px;width:1200px;height:486px}
.hero-photo{position:absolute;inset:0;background:linear-gradient(100deg,#8d9d7e 0%,#b8c6d6 30%,#d8e3ee 55%,#c4d3e3 100%)}
.hero-title{position:absolute;left:410px;top:66px;width:340px;text-align:center;color:var(--white);font-size:30px;font-weight:700;line-height:37px;text-shadow:0 2px 6px rgba(0,0,0,.35)}
.slider-dots{position:absolute;left:566px;top:434px;display:flex;gap:12px}
.slider-dots i{width:11px;height:11px;border-radius:50%;background:var(--white);display:block}
.slider-dots i.on{background:transparent;border:2px solid var(--white)}
.donate-form{position:absolute;left:757px;top:0;width:325px;height:486px;background:var(--red-soft)}
.donate-form h2{position:absolute;left:20px;top:24px;color:var(--white);font-size:21px;font-weight:700}
.donate-form h2::after{content:"";display:block;width:150px;height:2px;background:var(--white);margin-top:8px}
.field{position:absolute;height:40px;background:var(--white);font-size:11px;color:#8a8f96;padding-left:26px;line-height:40px}
.field::before{content:"";position:absolute;left:10px;top:16px;width:7px;height:7px;border:1px solid #9aa0a6;border-radius:2px}
.field.select::after{content:"";position:absolute;right:12px;top:18px;border:5px solid transparent;border-top-color:#555}
.btn-donate{position:absolute;left:130px;top:408px;width:175px;height:44px;background:var(--red);color:var(--white);font-size:15px;font-weight:700;text-align:center;line-height:44px}

/* intro */
.section-title{font-size:22px;font-weight:700;color:var(--heading);text-transform:uppercase}
.section-title.rule::after{content:"";display:block;width:92px;height:3px;background:var(--heading);margin-top:16px}
.benefit{position:absolute;left:133px;display:flex;align-items:center;gap:24px;font-size:14px;color:var(--ink)}
.ring-icon{width:44px;height:44px;border-radius:50%;border:2px solid var(--blue);display:flex;align-items:center;justify-content:center}
.col-divider{position:absolute;left:563px;top:670px;width:1px;height:535px;background:var(--line)}
.trust-badge{position:absolute;top:1162px;height:46px}
.step{position:absolute;left:637px;width:435px;height:118px}
.step-label{position:absolute;left:208px;top:38px;font-size:23px;font-weight:600}

/* why section */
.why{position:absolute;left:0;top:1307px;width:1200px;height:683px;background:var(--blue);color:var(--white)}
.why .section-title{color:var(--white);text-transform:uppercase;position:absolute;left:129px;top:52px;font-size:25px}
.why .section-title::after{content:"";display:block;width:174px;height:2px;background:var(--white);margin-top:16px}
.reason{position:absolute;width:440px}
.reason svg{position:absolute;left:-64px;top:0}
.reason h3{font-size:14px;font-weight:700;margin-bottom:8px}
.reason p{font-size:13px;line-height:20px}

/* program */
.program-title{position:absolute;left:0;width:1200px;top:2058px;text-align:center;font-size:22px;font-weight:700;color:var(--heading)}
.program-title::after{content:"";display:block;width:120px;height:3px;background:var(--heading);margin:22px auto 0}
.feature{position:absolute;top:2189px;width:200px;text-align:center;font-size:13px;font-weight:600;color:var(--ink);line-height:18px}
.feature .circle{width:124px;height:124px;margin:0 auto 36px;border-radius:50%;border:2px solid var(--blue);display:flex;align-items:center;justify-content:center}

/* footer */
.site-footer{position:absolute;left:0;top:2468px;width:1200px;height:263px;background:var(--blue);color:var(--white)}
.site-footer .brand{left:128px;top:58px}
.footer-divider{position:absolute;left:457px;top:40px;width:2px;height:110px;background:rgba(255,255,255,.8)}
.footer-menu{position:absolute;left:526px;top:48px}
.footer-menu h4{font-size:11px;font-weight:700;margin-bottom:20px}
.footer-menu p{font-size:12px}
.footer-rule{position:absolute;left:129px;top:165px;width:936px;height:1px;background:rgba(255,255,255,.35)}
.follow{position:absolute;left:133px;top:204px;display:flex;align-items:center;gap:10px;font-size:11px;font-weight:700}
.follow i{width:28px;height:28px;border-radius:50%;background:var(--white);display:block}
.legal{position:absolute;right:135px;top:210px;font-size:11px}
.ribbon{position:absolute;left:974px;top:2444px;width:91px;height:114px}
</style>
</head>
<body>

<header class="site-header">
  <div class="brand"><span class="brand-dot"></span>Wheels for Servicemen</div>
  <nav class="main-nav">
    <div class="nav-item active">
      <svg width="24" height="24" viewBox="0 0 24 24" fill="none" stroke="#fff" stroke-width="1.6"><path d="M3 11l9-8 9 8M5 9v12h5v-6h4v6h5V9"/></svg>
      <span>HOME</span></div>
    <div class="nav-item">
      <svg width="24" height="24" viewBox="0 0 24 24" fill="none" stroke="#fff" stroke-width="1.6"><circle cx="12" cy="12" r="3.5"/><circle cx="12" cy="12" r="9" stroke-dasharray="4 2.5"/></svg>
      <span>HOW IT WORKS</span></div>
    <div class="nav-item">
      <svg width="26" height="24" viewBox="0 0 26 24" fill="none" stroke="#fff" stroke-width="1.6"><rect x="2" y="4" width="22" height="16"/><path d="M2 4l11 9 11-9"/></svg>
      <span>CONTACT US</span></div>
  </nav>
  <div class="help-box">
    <svg width="44" height="44" viewBox="0 0 44 44" fill="none" stroke="#fff" stroke-width="2.4"><path d="M8 24v-4a14 14 0 0 1 28 0v4"/><rect x="5" y="22" width="7" height="11" rx="2"/><rect x="32" y="22" width="7" height="11" rx="2"/><path d="M35 33c0 5-5 7-11 7"/></svg>
    <div class="help-label">WE NEED YOUR HELP</div>
    <div class="help-phone">1-800-555-0142</div>
    <div class="help-note">Live Operators Available</div>
    <div class="help-days">7 DAYS A WEEK</div>
  </div>
</header>

<section class="hero">
  <div class="hero-photo" role="img" aria-label="Photo of a soldier in camouflage hugging a child wrapped in a flag, with a white car in falling snow"></div>
  <h1 class="hero-title">Donate Your Car:<br>Full Tax Deduction -<br>Running or Not</h1>
  <div class="slider-dots"><i class="on"></i><i></i><i></i><i></i></div>
  <form class="donate-form">
    <h2>DONATE HERE</h2>
    <div class="field" style="left:24px;top:92px;width:281px">Name</div>
    <div class="field" style="left:24px;top:141px;width:281px">E mail</div>
    <div class="field" style="left:24px;top:191px;width:133px">Phone</div>
    <div class="field" style="left:170px;top:191px;width:135px">Mobile</div>
    <div class="field" style="left:24px;top:240px;width:281px">Address</div>
    <div class="field" style="left:24px;top:290px;width:133px">City</div>
    <div class="field select" style="left:170px;top:290px;width:135px">State</div>
    <div class="field" style="left:24px;top:340px;width:281px">Zip Code</div>
    <div class="btn-donate">DONATE NOW &nbsp;›</div>
  </form>
</section>

<h2 class="section-title rule abs" style="left:129px;top:666px">Donate Your Car Today!</h2>
<div class="benefit" style="top:739px"><span class="ring-icon"><svg width="18" height="20" viewBox="0 0 18 20" fill="none" stroke="#1e5aa8" stroke-width="1.8"><path d="M13 5c-1-2-8-2-8 1.5S13 9 13 13.5 5 17 4 14M9 1v18"/></svg></span>You have no costs.</div>
<div class="benefit" style="top:796px"><span class="ring-icon"><svg width="24" height="16" viewBox="0 0 24 16" fill="none" stroke="#1e5aa8" stroke-width="1.6"><path d="M2 12V6h9l3 6h8"/><circle cx="6" cy="13" r="2"/><circle cx="18" cy="13" r="2"/></svg></span>Free towing, running or not.</div>
<div class="benefit" style="top:852px"><span class="ring-icon"><svg width="16" height="20" viewBox="0 0 16 20" fill="none" stroke="#1e5aa8" stroke-width="1.6"><rect x="1" y="1" width="14" height="18"/><path d="M4 6h8M4 10h8M4 14h5"/></svg></span>We issue you an IRS tax receipt.</div>
<div class="benefit" style="top:908px"><span class="ring-icon"><svg width="16" height="20" viewBox="0 0 16 20" fill="#1e5aa8"><path d="M1 1h9l5 5v13H1z"/><path d="M4 10h8M4 14h8" stroke="#fff" stroke-width="1.5"/></svg></span>We take care of all paperwork.</div>
<div class="benefit" style="top:963px"><span class="ring-icon"><svg width="20" height="18" viewBox="0 0 20 18"><path d="M10 1l9 16H1z" fill="#1e5aa8"/><path d="M10 7v5M10 14v1.5" stroke="#fff" stroke-width="1.8"/></svg></span>And we take care of DMV &amp; Smog issues.</div>

<h2 class="section-title abs" style="left:129px;top:1080px">Safe &amp; Secure</h2>
<div class="trust-badge" style="left:129px;width:112px;border-radius:4px;background:#e8ebef"></div>
<div class="trust-badge" style="left:302px;width:66px;height:54px;top:1158px;border-radius:50%;background:#cfe0ee;border:3px solid #9bbad6"></div>

<div class="col-divider"></div>

<h2 class="section-title rule abs" style="left:637px;top:656px">How It Works</h2>
<div class="step" style="top:757px">
  <svg width="435" height="118" viewBox="0 0 435 118" fill="none" stroke="#1e5aa8" stroke-width="3"><path d="M59 4h317a55 55 0 0 1 0 110H59"/><circle cx="59" cy="59" r="55"/><circle cx="59" cy="59" r="42" fill="#1e5aa8" stroke="none"/><path d="M47 45c-3 3-1 13 7 21s18 10 21 7l-5-6-5 3c-3-1-10-8-11-11l3-5z" fill="none" stroke="#fff" stroke-width="2.4"/></svg>
  <span class="step-label" style="color:var(--blue)">Call us</span>
</div>
<div class="step" style="top:924px">
  <svg width="435" height="118" viewBox="0 0 435 118" fill="none" stroke="#f6c22b" stroke-width="3"><path d="M59 4h317a55 55 0 0 1 0 110H59"/><circle cx="59" cy="59" r="55" stroke="#f39c1e"/><circle cx="59" cy="59" r="42" fill="#f39c1e" stroke="none"/><path d="M40 68V56h14l5 10h17M48 56l-2-10h8" stroke="#fff" stroke-width="2.4"/><circle cx="46" cy="70" r="4" fill="#fff" stroke="none"/><circle cx="70" cy="70" r="4" fill="#fff" stroke="none"/></svg>
  <span class="step-label" style="color:var(--orange)">We Tow it</span>
</div>
<div class="step" style="top:1101px">
  <svg width="435" height="118" viewBox="0 0 435 118" fill="none" stroke="#1e9ee0" stroke-width="3"><path d="M59 4h317a55 55 0 0 1 0 110H59"/><circle cx="59" cy="59" r="55"/><circle cx="59" cy="59" r="42" fill="#1e9ee0" stroke="none"/><rect x="46" y="43" width="26" height="32" stroke="#fff" stroke-width="2.4"/><path d="M51 52h16M51 59h16M51 66h10" stroke="#fff" stroke-width="2"/></svg>
  <span class="step-label" style="color:var(--sky)">Tax Write Off</span>
</div>

<section class="why">
  <h2 class="section-title">Why Donate Your Car To Us?</h2>
  <div class="reason" style="left:220px;top:166px">
    <svg width="44" height="44" viewBox="0 0 44 44" fill="none" stroke="#fff" stroke-width="2.2"><path d="M8 10c-4 4-1 16 9 26s22 13 26 9l-6-7-6 3c-4-1-13-10-14-14l3-6z"/><text x="24" y="22" fill="#fff" stroke="none" font-size="12" font-weight="700" font-family="Open Sans,sans-serif">24</text></svg>
    <h3>IRS 501(c)3 Approved:</h3><p>Free 24/7 Pickup with No DMV Hassles.</p></div>
  <div class="reason" style="left:717px;top:166px">
    <svg width="44" height="30" viewBox="0 0 44 30" fill="none" stroke="#fff" stroke-width="2.2"><path d="M4 24V14l6-10h24l6 10v10zM4 14h36"/><circle cx="12" cy="19" r="2" fill="#fff"/><circle cx="32" cy="19" r="2" fill="#fff"/></svg>
    <h3>All Cars Accepted</h3><p>We take your car regardless of its condition or registration status.</p></div>
  <div class="reason" style="left:220px;top:289px">
    <svg width="50" height="40" viewBox="0 0 50 40" fill="none" stroke="#fff" stroke-width="2.2"><path d="M2 32V20h18l6 12h20M12 20l-3-14h10"/><circle cx="10" cy="33" r="4" fill="#fff"/><circle cx="38" cy="33" r="4" fill="#fff"/></svg>
    <h3>Free Local Towing to You</h3><p>We will pick up your car donation, running or not, when it's most convenient, at home or work.</p></div>
  <div class="reason" style="left:717px;top:289px">
    <svg width="44" height="44" viewBox="0 0 44 44" fill="#fff"><rect x="16" y="2" width="20" height="14" rx="2"/><path d="M6 26l10-6h14v5H20M6 40V26M10 40l20-2 10-12-4-3-10 8"/></svg>
    <h3>Income Tax Deduction</h3><p>We issue you an IRS tax receipt &amp; offer the largest resale network to get you the highest tax write-off possible.</p></div>
  <div class="reason" style="left:220px;top:415px">
    <svg width="40" height="44" viewBox="0 0 40 44" fill="none" stroke="#fff" stroke-width="2.2"><rect x="4" y="8" width="26" height="32"/><path d="M10 4h26v32M10 18h14M10 25h14M10 32h10"/></svg>
    <h3>No Paperwork Hassles</h3><p>We take any car and handle everything: DMV, Smog and IRS paperwork.</p></div>
  <div class="reason" style="left:717px;top:415px">
    <svg width="46" height="46" viewBox="0 0 46 46" fill="none" stroke="#fff" stroke-width="2.2"><circle cx="23" cy="23" r="19"/><path d="M11 28v-7l5-7h14l5 7v7z" fill="#fff"/></svg>
    <h3>Car donations help fund programs</h3><p>And benefit National Servicemen Support Fund. An IRS 501(c)3 nonprofit organization.</p></div>
  <div class="reason" style="left:220px;top:548px">
    <svg width="46" height="46" viewBox="0 0 46 46"><path d="M23 2l5 5 7-2 1 7 7 2-2 7 5 5-5 5 2 7-7 2-1 7-7-2-5 5-5-5-7 2-1-7-7-2 2-7-5-5 5-5-2-7 7-2 1-7 7 2z" fill="#fff"/><text x="23" y="27" text-anchor="middle" fill="#1e5aa8" font-size="10" font-weight="800" font-family="Open Sans,sans-serif">FREE</text></svg>
    <h3>Schedule a Free Pickup</h3><p>Complete the form and a representative will call you to arrange a convenient time to pickup your car.</p></div>
  <div class="reason" style="left:717px;top:548px">
    <svg width="46" height="46" viewBox="0 0 46 46" fill="none" stroke="#fff" stroke-width="2.2"><path d="M40 23A17 17 0 1 1 23 6"/><path d="M23 12v11l6 4"/><text x="24" y="40" fill="#fff" stroke="none" font-size="10" font-weight="700" font-family="Open Sans,sans-serif">24/7</text></svg>
    <h3>7 Days a week</h3><p>And benefit National Servicemen Support Fund. An IRS 501(c)3 nonprofit organization.</p></div>
</section>

<h2 class="program-title">CAR DONATION PROGRAM</h2>
<div class="feature" style="left:151px"><div class="circle"><svg width="56" height="56" viewBox="0 0 56 56" fill="none" stroke="#1e5aa8" stroke-width="2.4"><circle cx="28" cy="28" r="24"/><ellipse cx="28" cy="28" rx="11" ry="24"/><path d="M4 28h48M8 16h40M8 40h40"/></svg></div>Donations Accepted<br>Nationwide</div>
<div class="feature" style="left:390px"><div class="circle"><svg width="56" height="44" viewBox="0 0 56 44" fill="#1e5aa8"><path d="M6 36V22l7-14h30l7 14v14z"/><path d="M14 20l4-8h20l4 8z" fill="#fff"/><circle cx="15" cy="28" r="3" fill="#fff"/><circle cx="41" cy="28" r="3" fill="#fff"/><rect x="8" y="36" width="8" height="6"/><rect x="40" y="36" width="8" height="6"/></svg></div>All vehicle<br>types welcome</div>
<div class="feature" style="left:617px"><div class="circle"><svg width="44" height="44" viewBox="0 0 44 44" fill="none" stroke="#1e5aa8" stroke-width="2.6"><path d="M36 8L8 36"/><circle cx="12" cy="12" r="6"/><circle cx="32" cy="32" r="6"/></svg></div>Tax<br>Deductible</div>
<div class="feature" style="left:845px"><div class="circle"><svg width="62" height="50" viewBox="0 0 62 50" fill="#1e5aa8"><path d="M4 38V24h22l6 10h26v4z"/><path d="M10 24l-2-18h4l4 18" /><path d="M10 6l14 18" stroke="#1e5aa8" stroke-width="2.4"/><circle cx="14" cy="40" r="5"/><circle cx="46" cy="40" r="5"/></svg></div>Towling<br>is free</div>

<footer class="site-footer">
  <div class="brand"><span class="brand-dot"></span>Wheels for Servicemen</div>
  <div class="footer-divider"></div>
  <div class="footer-menu"><h4>MENU</h4><p>Home &nbsp;|&nbsp; About Us &nbsp;|&nbsp; How it works &nbsp;|&nbsp; Contact us</p></div>
  <div class="footer-rule"></div>
  <div class="follow">FOLLOW US : &nbsp;<i></i><i></i><i></i></div>
  <div class="legal">Privacy Policy &nbsp;|&nbsp; Copyrights @ 2016 All Rights Reserved</div>
</footer>
<svg class="ribbon" viewBox="0 0 91 114" aria-hidden="true"><path d="M4 2h83v92l-41.5 18L4 94z" fill="#e9ecf0" stroke="#c9ced6" stroke-width="2"/><rect x="14" y="10" width="63" height="40" fill="#1e5aa8"/></svg>

</body>
</html>
```